KAJU Freightways #ALLKAJU Business Cards & Letterhead

I am looking to business cards designed for our organization. We are currently undergoing a small re-branding that is taking place. Our organization is called KAJU Freightways and we are headquartered in Phoenix, AZ. We primarily provide transportation and logistics services to the Marlow Parcel Bureau who is our largest customer. I would like to see a design that incorporates name, title, contact info, website, and address (this will be different depending on the employee). I would also like to see some color on the business card using our logo colors or a variation. I would like our logo on the back of the business card with the website displayed. The final design should communicate that we are a next generation transportation operate that focuses on being driver-first, customer-centric, innovative, and sustainable.We would also like our #ALLKAJU catch phrase incorporated as well.

Target Market(s)

Transportation & Logistics

Industry/Entity Type

Trucking Company

Contact Information for Business Card

-First and Last Name
-Position Title
-Contact Phone
-Contact Email
-Physical Address

Font styles to use
Serif

Colors

Designer to choose colors to be used in the design.

Requirements
Must have
• -KAJU logo prominently displayed
• -#ALLKAJU catch phrase used
• -Some amount of color, design gradient, etc.
• -Logo on the back with website listed (https://www.kajufreightco.example)

```html
<!DOCTYPE html>
<html lang="en">
<head>
<meta charset="utf-8">
<title>KAJU Freightways Business Card</title>
<link rel="stylesheet" href="https://fonts.googleapis.com/css2?family=Lora:wght@400;500;600&display=swap">
<style>
  :root {
    --backdrop: #141414;
    --card: #1e1e1e;
    --card-edge: #262626;
    --silver: #cfcfcf;
    --silver-soft: #a9a9a9;
    --accent: #2fb3c6;
    --accent-deep: #1d6fa3;
  }
  * { margin: 0; padding: 0; box-sizing: border-box; }
  html, body {
    width: 1200px; height: 900px; overflow: hidden;
    background: var(--backdrop);
    font-family: "Lora", serif;
    color: var(--silver);
  }
  .canvas {
    width: 1200px; height: 900px;
    display: flex; flex-direction: column; align-items: center; justify-content: center;
    gap: 30px;
  }
  .card {
    position: relative;
    width: 700px; height: 400px;
    background: linear-gradient(135deg, var(--card) 0%, #1a1a1a 60%, var(--card-edge) 100%);
    box-shadow: 0 10px 30px rgba(0,0,0,.6);
    overflow: hidden;
  }
  .card::after {
    content: ""; position: absolute; left: 0; right: 0; bottom: 0; height: 5px;
    background: linear-gradient(90deg, var(--accent-deep), var(--accent));
  }
  .brand-mark {
    display: flex; align-items: center; justify-content: center;
    border: 3px solid var(--silver);
    border-radius: 50%;
    flex: none;
  }
  .brand-name {
    font-weight: 600;
    letter-spacing: 2px;
    color: var(--silver);
  }
  .tagline {
    font-weight: 600;
    letter-spacing: 3px;
    color: var(--accent);
  }
  /* back of card */
  .card--back { display: flex; flex-direction: column; align-items: center; }
  .card--back .brand-mark { width: 190px; height: 190px; margin-top: 60px; }
  .card--back .brand-name { font-size: 46px; }
  .card--back .tagline { font-size: 18px; margin-top: 22px; }
  .card--back .website {
    position: absolute; bottom: 36px;
    font-size: 17px; letter-spacing: 2px; color: var(--silver-soft);
  }
  /* front of card */
  .card--front { display: flex; align-items: center; }
  .card--front .brand-mark { width: 240px; height: 240px; margin-left: 55px; }
  .card--front .brand-name { font-size: 58px; }
  .divider {
    width: 2px; height: 250px; flex: none;
    background: linear-gradient(180deg, var(--accent), var(--accent-deep));
    margin: 0 40px;
  }
  .contact { display: flex; flex-direction: column; width: 320px; }
  .contact__name { font-size: 27px; font-weight: 600; letter-spacing: 1px; }
  .contact__title { font-size: 16px; color: var(--accent); margin-bottom: 18px; }
  .contact__address { font-size: 17px; line-height: 1.35; margin-bottom: 14px; }
  .contact__line { display: flex; align-items: center; gap: 10px; font-size: 17px; line-height: 1.55; white-space: nowrap; }
  .contact__line svg { width: 13px; height: 13px; flex: none; color: var(--accent); }
  .contact .tagline { font-size: 14px; margin-top: 12px; }
</style>
</head>
<body>
<main class="canvas">
  <section class="card card--back">
    <div class="brand-mark"><span class="brand-name">KAJU</span></div>
    <p class="tagline">#ALLKAJU</p>
    <p class="website">www.kajufreightco.example</p>
  </section>

  <section class="card card--front">
    <div class="brand-mark"><span class="brand-name">KAJU</span></div>
    <div class="divider"></div>
    <div class="contact">
      <p class="contact__name">DARREN COLE</p>
      <p class="contact__title">Director</p>
      <p class="contact__address">4120 North Cactus<br>Ridge Boulevard<br>Glendale, AZ 85308</p>
      <p class="contact__line">
        <svg viewBox="0 0 16 16" fill="none" stroke="currentColor" stroke-width="1.6"><path d="M4 1.5l2.5 3-1.5 1.5c.8 2 2.5 3.7 4.5 4.5l1.5-1.5 3 2.5-1.5 2.5C7 14 2 9 1.5 3z"/></svg>
        602-555-0148
      </p>
      <p class="contact__line">
        <svg viewBox="0 0 16 16" fill="none" stroke="currentColor" stroke-width="1.6"><rect x="1.5" y="3.5" width="13" height="9"/><path d="M1.5 3.5l6.5 5 6.5-5"/></svg>
        info@kajufreightco.example
      </p>
      <p class="contact__line">
        <svg viewBox="0 0 16 16" fill="none" stroke="currentColor" stroke-width="1.4"><circle cx="8" cy="8" r="6.5"/><ellipse cx="8" cy="8" rx="3" ry="6.5"/><path d="M1.5 8h13"/></svg>
        www.kajufreightco.example
      </p>
      <p class="tagline">#ALLKAJU</p>
    </div>
  </section>
</main>
</body>
</html>
```